Business Card for Coastal Tundrabridge Advisory

We need a business card for Coastal Tundrabridge Advisory. The company website address is provided below. The company logo is attached. We provide specialized permafrost services to the mining, transportation, and oil & gas industries. The card should be prepared for:
Matthias Korhonen, PhD.
Coastal Tundrabridge Advisory
PO Box 418259
Quillwater, Alaska 99642
Direct: +1-907-555-0143
Email: mkorhonen@tundrabridgeadvisory.example
Website: www.coastaltundrabridgeadvisory.example

```html
<!DOCTYPE html>
<html lang="en">
<head>
<meta charset="utf-8">
<title>Coastal Tundrabridge Advisory – Business Card</title>
<link rel="stylesheet" href="https://fonts.googleapis.com/css2?family=Quicksand:wght@500;600;700&display=swap">
<style>
  :root {
    --backdrop: #a9a9a9;
    --card-dark: #333333;
    --card-light: #ffffff;
    --brand-grey: #9b9b9b;
    --ink: #2f2f2f;
    --ink-soft: #3c3c3c;
    --ghost: #ededed;
  }
  * { margin: 0; padding: 0; box-sizing: border-box; }
  html, body {
    width: 1200px; height: 1000px; overflow: hidden;
    background: var(--backdrop);
    font-family: "Quicksand", sans-serif;
  }
  .card {
    position: absolute;
    width: 615px; height: 354px;
    border-radius: 16px;
    overflow: hidden;
    box-shadow: 0 3px 8px rgba(0,0,0,0.22);
  }
  .card--front { left: 294px; top: 132px; background: var(--card-dark); }
  .card--back  { left: 291px; top: 530px; background: var(--card-light); }

  .brand-name {
    position: absolute;
    font-weight: 700;
    color: var(--brand-grey);
    text-transform: uppercase;
    white-space: nowrap;
    text-align: center;
  }
  .card--front .brand-name {
    left: 0; right: 0; top: 160px;
    font-size: 23px; letter-spacing: 3px;
  }
  .card--back .brand-name {
    left: 40px; width: 245px; top: 160px;
    font-size: 13px; letter-spacing: 1.5px; line-height: 18px;
  }

  .contact {
    position: absolute; left: 310px; top: 100px;
    font-size: 13px; line-height: 16.8px;
    color: var(--ink-soft); font-weight: 500;
  }
  .contact__name { font-weight: 700; color: var(--ink); letter-spacing: 0.4px; }
  .contact__group + .contact__group { margin-top: 16.8px; }

  .ghost-name {
    position: absolute; left: -4px; bottom: -14px;
    font-size: 66px; font-weight: 600; letter-spacing: 4px;
    color: var(--ghost); white-space: nowrap; line-height: 1;
  }
</style>
</head>
<body>
  <section class="card card--front">
    <div class="brand-name">Coastal Tundrabridge Advisory</div>
  </section>

  <section class="card card--back">
    <div class="ghost-name" aria-hidden="true">TUNDRABRIDGE</div>
    <div class="brand-name">Coastal Tundrabridge<br>Advisory</div>
    <div class="contact">
      <div class="contact__group">
        <div class="contact__name">MATTHIAS KORHONEN, PHD.</div>
        <div>Coastal Tundrabridge Advisory</div>
      </div>
      <div class="contact__group">
        <div>PO Box 418259</div>
        <div>Quillwater, Alaska 99642</div>
      </div>
      <div class="contact__group">
        <div>(907) 555-0143</div>
        <div>mkorhonen@tundrabridgeadvisory.example</div>
        <div>coastaltundrabridgeadvisory.example</div>
      </div>
    </div>
  </section>
</body>
</html>
```